Business Card Design

New business card design

Target Market(s)

Residential & Commercial Property Managers

Industry/Entity Type

Plumbing Services

Contact Information for Business Card

Name - Rowan Keddle, title - Director, Phone Number - 0431 286 517, email - rowan@tbk-plumbing.com.au, Company ABN - 73 215 904 386,

Font styles to use
Sans Serif

Colors
0054AA
0677BA
7BADD7
CADEEF
E8F1F8

```html
<!DOCTYPE html>
<html lang="en">
<head>
<meta charset="utf-8">
<title>TBK Plumbing Services – Business Card</title>
<link rel="stylesheet" href="https://fonts.googleapis.com/css2?family=Roboto:wght@300;400;500;700&display=swap">
<style>
  :root {
    --blue-deep: #0054AA;
    --blue-mid: #0677BA;
    --blue-soft: #7BADD7;
    --blue-pale: #CADEEF;
    --blue-mist: #E8F1F8;
    --accent: #1AA3E8;
    --sky: #3FA9DB;
    --ink: #1f1f1f;
    --ink-soft: #555555;
    --paper: #F7F7F7;
    --stage: #1E1E1E;
  }
  * { box-sizing: border-box; margin: 0; padding: 0; }
  html, body { width: 1200px; height: 852px; overflow: hidden; }
  body {
    background: var(--stage);
    font-family: "Roboto", Arial, sans-serif;
    position: relative;
  }
  .card {
    position: absolute;
    top: 267px;
    width: 520px;
    height: 318px;
    border-radius: 22px;
    overflow: hidden;
  }
  .card--front { left: 50px; background: var(--blue-deep); }
  .card--back { left: 630px; background: var(--paper); }

  .front-backdrop {
    position: absolute;
    inset: 0;
    background: linear-gradient(170deg, var(--sky) 0%, var(--blue-mid) 45%, var(--blue-deep) 100%);
  }

  .wordmark {
    position: absolute;
    color: #ffffff;
    font-weight: 300;
    text-align: center;
    line-height: 1;
  }
  .card--front .wordmark { left: 0; right: 0; top: 100px; }
  .wordmark__name { display: block; font-size: 96px; letter-spacing: 4px; }
  .wordmark__tag {
    display: block;
    font-size: 13px;
    letter-spacing: 9px;
    margin-top: 8px;
    text-transform: lowercase;
  }

  .card--back .wordmark {
    color: var(--ink);
    right: 34px; top: 28px;
    text-align: right;
  }
  .card--back .wordmark__name { font-size: 62px; letter-spacing: 3px; }
  .card--back .wordmark__tag { font-size: 9px; letter-spacing: 6px; margin-top: 4px; }

  .person {
    position: absolute;
    right: 34px; top: 126px;
    text-align: right;
  }
  .person__name { font-size: 18px; font-weight: 700; color: var(--ink); }
  .person__title { font-size: 12px; font-weight: 300; color: var(--ink-soft); margin-top: 2px; }

  .contact {
    position: absolute;
    right: 34px; top: 188px;
    list-style: none;
    text-align: right;
  }
  .contact__item {
    display: flex;
    justify-content: flex-end;
    align-items: center;
    gap: 10px;
    font-size: 12.5px;
    font-weight: 400;
    color: var(--ink);
    line-height: 21px;
  }
  .contact__icon { width: 12px; height: 12px; flex: none; }

  .back-band {
    position: absolute;
    left: 0; right: 0; bottom: 0;
    height: 14px;
    background: var(--accent);
  }
  .back-accent {
    position: absolute;
    left: 0; bottom: 0;
    width: 120px; height: 30px;
    background: var(--accent);
    clip-path: polygon(0 0, 70% 55%, 100% 55%, 100% 100%, 0 100%);
  }
</style>
</head>
<body>

  <section class="card card--front" aria-label="Business card front">
    <div class="front-backdrop" role="img" aria-label="Layered blue water wave background"></div>
    <div class="wordmark">
      <span class="wordmark__name">tbk</span>
      <span class="wordmark__tag">plumbing services</span>
    </div>
  </section>

  <section class="card card--back" aria-label="Business card back">
    <div class="wordmark">
      <span class="wordmark__name">tbk</span>
      <span class="wordmark__tag">plumbing services</span>
    </div>

    <div class="person">
      <p class="person__name">Rowan Keddle</p>
      <p class="person__title">Director</p>
    </div>

    <ul class="contact">
      <li class="contact__item">0431 286 517
        <svg class="contact__icon" viewBox="0 0 12 12" aria-hidden="true"><path d="M2 1h2.5l1 3-1.5 1a6 6 0 0 0 3 3l1-1.5 3 1V10a1 1 0 0 1-1 1A9 9 0 0 1 1 2a1 1 0 0 1 1-1z" fill="#0677BA"/></svg>
      </li>
      <li class="contact__item">rowan@tbk-plumbing.com.au
        <svg class="contact__icon" viewBox="0 0 12 12" aria-hidden="true"><rect x="0.5" y="2" width="11" height="8" rx="1" fill="#0677BA"/><path d="M1 2.5l5 4 5-4" stroke="#fff" stroke-width="1" fill="none"/></svg>
      </li>
      <li class="contact__item">www.tbk-plumbing.com.au
        <svg class="contact__icon" viewBox="0 0 12 12" aria-hidden="true"><circle cx="6" cy="6" r="5.2" fill="#0677BA"/><path d="M1 6h10M6 1c-2.5 3-2.5 7 0 10M6 1c2.5 3 2.5 7 0 10" stroke="#fff" stroke-width="0.8" fill="none"/></svg>
      </li>
      <li class="contact__item">ABN - 73 215 904 386
        <svg class="contact__icon" viewBox="0 0 12 12" aria-hidden="true"><path d="M4 1L3 11M9 1L8 11M1 4h10M1 8h10" stroke="#0677BA" stroke-width="1.3" fill="none"/></svg>
      </li>
    </ul>

    <div class="back-band"></div>
    <div class="back-accent"></div>
  </section>

</body>
</html>
```